New Company Business Card design

Looking for a corporate looking business card utilising my new logo design - the logo i would like embossed as one option and flat as another - simplistic but stylish - less is more - we are an import export business launching into the market - i would like a couple of options as main background - Grey or Black

```html
<!DOCTYPE html>
<html lang="en">
<head>
<meta charset="utf-8">
<title>Meridian Trade Partners – Business Card</title>
<link href="https://fonts.googleapis.com/css2?family=Roboto:wght@400;500;700&display=swap" rel="stylesheet">
<style>
  :root {
    --stage: #ece8e2;
    --card-light: #f4f4f4;
    --card-dark: #1c1d1f;
    --brand-blue: #1479c4;
    --accent-grey: #6d6e71;
    --ink-white: #ffffff;
  }
  * { margin: 0; padding: 0; box-sizing: border-box; }
  html, body { width: 1200px; height: 960px; overflow: hidden; }
  body {
    background: var(--stage);
    font-family: "Roboto", Arial, sans-serif;
    position: relative;
  }
  .card {
    position: absolute;
    width: 600px;
    height: 343px;
    overflow: hidden;
  }
  .card--front { left: 314px; top: 113px; background: var(--card-light); }
  .card--back { left: 311px; top: 472px; background: var(--card-dark); }

  .front-logo {
    position: absolute;
    left: 30px;
    top: 120px;
    width: 250px;
    text-align: center;
    color: var(--brand-blue);
    font-weight: 500;
    font-size: 21px;
    line-height: 1.25;
    letter-spacing: 0.5px;
  }
  .contact-band {
    position: absolute;
    left: 304px;
    top: 59px;
  }
  .contact {
    position: absolute;
    left: 391px;
    top: 86px;
    color: var(--ink-white);
  }
  .contact__name { font-size: 22px; font-weight: 700; letter-spacing: 0.3px; line-height: 1; }
  .contact__role { font-size: 14.5px; font-weight: 500; margin-top: 5px; }
  .contact__address { font-size: 14px; line-height: 18px; margin-top: 9px; }
  .contact__list { list-style: none; margin-top: 8px; font-size: 14px; }
  .contact__list li { display: flex; align-items: center; height: 19px; }
  .contact__list svg { width: 13px; height: 13px; margin-right: 9px; fill: var(--ink-white); }

  .back-name {
    position: absolute;
    left: 282px;
    top: 170px;
    color: var(--ink-white);
    font-size: 140px;
    font-weight: 400;
    line-height: 1;
    letter-spacing: -2px;
    white-space: nowrap;
  }
  .back-url {
    position: absolute;
    left: 284px;
    top: 297px;
    color: var(--ink-white);
    font-size: 14px;
  }
</style>
</head>
<body>
  <section class="card card--front" aria-label="Business card front">
    <div class="front-logo">MERIDIAN TRADE<br>PARTNERS</div>

    <svg class="contact-band" width="296" height="226" viewBox="0 0 296 226" aria-hidden="true">
      <path d="M113 0 H296 V226 H113 A113 113 0 0 1 113 0 Z" fill="var(--accent-grey)"/>
      <path d="M133 3 H296 V225 H133 A111 111 0 0 1 133 3 Z" fill="var(--brand-blue)"/>
    </svg>

    <div class="contact">
      <p class="contact__name">DANIEL REYES</p>
      <p class="contact__role">CEO/FOUNDER</p>
      <p class="contact__address">214 Harbor View Road<br>Juneau, Alaska 99801</p>
      <ul class="contact__list">
        <li><svg viewBox="0 0 24 24"><path d="M6.6 10.8a15.1 15.1 0 0 0 6.6 6.6l2.2-2.2a1 1 0 0 1 1-.25 11.4 11.4 0 0 0 3.6.57 1 1 0 0 1 1 1V20a1 1 0 0 1-1 1A17 17 0 0 1 3 4a1 1 0 0 1 1-1h3.5a1 1 0 0 1 1 1c0 1.25.2 2.45.57 3.57a1 1 0 0 1-.25 1z"/></svg>555 210 4481</li>
        <li><svg viewBox="0 0 24 24"><path d="M7 1h10a2 2 0 0 1 2 2v18a2 2 0 0 1-2 2H7a2 2 0 0 1-2-2V3a2 2 0 0 1 2-2zm0 3v14h10V4zm5 15.5a1 1 0 1 0 0 2 1 1 0 0 0 0-2z"/></svg>555 318 7720</li>
        <li><svg viewBox="0 0 24 24"><path d="M6 2h12v5H6zM3 8h18a2 2 0 0 1 2 2v7h-4v5H5v-5H1v-7a2 2 0 0 1 2-2zm4 8v4h10v-4z"/></svg>555 902 3365</li>
        <li><svg viewBox="0 0 24 24"><path d="M2 5h20v14H2zm2 2v.5l8 5 8-5V7l-8 5z"/></svg>hello@meridiantrade.com</li>
      </ul>
    </div>
  </section>

  <section class="card card--back" aria-label="Business card back">
    <p class="back-name">MTP</p>
    <p class="back-url">www.meridiantradepartners.com</p>
  </section>
</body>
</html>
```